Northfield Builders Guild Business card

We are looking for a new business card design with photo included.
Our business is a nonprofit construction contractor membership organization. We offer business education, assist with business setup and licensing, provide safety training, and provide a member directory.
URL: www.builderslinkguild.org
Color code:
CMYK: 0 cyan, 42 magenta, 100 yellow, 0 black for Print.
Hexidecimal: #FF9900
RGB: R 255; G 153; B 0

```html
<!DOCTYPE html>
<html lang="en">
<head>
<meta charset="utf-8">
<title>Northfield Builders Guild – Business Card</title>
<link rel="stylesheet" href="https://fonts.googleapis.com/css2?family=Roboto:wght@400;500;700&display=swap">
<style>
  :root {
    --backdrop: #cccccc;
    --card: #232323;
    --accent: #ff9900;
    --text: #ffffff;
    --rule: #5a5a5a;
  }
  * { margin: 0; padding: 0; box-sizing: border-box; }
  html, body { width: 1065px; height: 1200px; overflow: hidden; }
  body {
    background: var(--backdrop);
    font-family: "Roboto", Arial, sans-serif;
    position: relative;
    color: var(--text);
  }
  .card { position: absolute; width: 585px; height: 363px; }
  .card-shape { position: absolute; inset: 0; width: 100%; height: 100%; }
  .card-shape path { fill: var(--card); }
  .card--front { left: 292px; top: 218px; }
  .card--back { left: 263px; top: 623px; }

  .front-brand {
    position: absolute; left: 46px; top: 55px; width: 84px; height: 251px;
    display: flex; flex-direction: column; justify-content: center; align-items: flex-start; gap: 6px;
    writing-mode: vertical-rl; transform: rotate(180deg);
    font-weight: 700; color: var(--text); line-height: 1; white-space: nowrap;
    overflow: hidden;
  }
  .front-brand .brand-line--top { font-size: 40px; }
  .front-brand .brand-line--bottom { font-size: 30px; }

  .divider {
    position: absolute; left: 148px; top: 64px; width: 1px; height: 235px;
    background: var(--rule);
  }
  .person { position: absolute; left: 171px; top: 64px; }
  .person-name { font-size: 22px; font-weight: 700; color: var(--accent); letter-spacing: 0.2px; }
  .person-title { font-size: 14.5px; font-weight: 400; margin-top: 2px; letter-spacing: 0.2px; }

  .contacts { position: absolute; left: 169px; top: 124px; list-style: none; }
  .contacts li {
    display: flex; align-items: center; gap: 5px;
    height: 22px; font-size: 17.5px; line-height: 1;
  }
  .contacts .icon { width: 21px; height: 21px; flex: none; }
  .contacts .icon circle { fill: var(--accent); }
  .contacts .icon .glyph { fill: none; stroke: var(--card); stroke-width: 1.4; stroke-linecap: round; stroke-linejoin: round; }
  .accent { color: var(--accent); }

  .address { position: absolute; left: 171px; top: 252px; font-size: 17.5px; line-height: 21px; }

  .back-brand {
    position: absolute; left: 134px; top: 128px; width: 320px;
    text-align: center; font-weight: 700; color: var(--text); line-height: 1;
  }
  .back-brand .brand-line--top { font-size: 50px; display: block; }
  .back-brand .brand-line--bottom { font-size: 35px; display: block; margin-top: 6px; letter-spacing: 0.5px; }
</style>
</head>
<body>

<section class="card card--front" aria-label="Business card front">
  <svg class="card-shape" viewBox="0 0 585 363" aria-hidden="true">
    <path d="M0 0 H403.5 A181.5 181.5 0 0 1 403.5 363 H0 Z"/>
  </svg>

  <div class="front-brand">
    <span class="brand-line--top">NORTHFIELD</span>
    <span class="brand-line--bottom">BUILDERS GUILD</span>
  </div>

  <div class="divider"></div>

  <div class="person">
    <p class="person-name">DANIEL HARPER</p>
    <p class="person-title">MANAGING DIRECTOR</p>
  </div>

  <ul class="contacts">
    <li>
      <svg class="icon" viewBox="0 0 21 21" aria-hidden="true"><circle cx="10.5" cy="10.5" r="10.5"/>
        <path class="glyph" d="M6.5 5.5 l2 -0.5 1.3 3 -1.3 1 a6 6 0 0 0 3 3 l1 -1.3 3 1.3 -0.5 2 a1.5 1.5 0 0 1 -1.6 1 a9 9 0 0 1 -7.9 -7.9 a1.5 1.5 0 0 1 1 -1.6 z"/></svg>
      <span>(971) 555-0142 <span class="accent">(Office)</span></span>
    </li>
    <li>
      <svg class="icon" viewBox="0 0 21 21" aria-hidden="true"><circle cx="10.5" cy="10.5" r="10.5"/>
        <rect class="glyph" x="7" y="5" width="7" height="11" rx="1"/><path class="glyph" d="M10 14.2 h1"/></svg>
      <span>800-555-0198</span>
    </li>
    <li>
      <svg class="icon" viewBox="0 0 21 21" aria-hidden="true"><circle cx="10.5" cy="10.5" r="10.5"/>
        <path class="glyph" d="M7.5 8.5 V5.5 h6 v3 M5.5 8.5 h10 v5 h-2 M7.5 13.5 h-2 v-5 M7.5 11.5 h6 v4 h-6 z"/></svg>
      <span>503.555.0176</span>
    </li>
    <li>
      <svg class="icon" viewBox="0 0 21 21" aria-hidden="true"><circle cx="10.5" cy="10.5" r="10.5"/>
        <rect class="glyph" x="5" y="7" width="11" height="7.5"/><path class="glyph" d="M5 7 l5.5 4.5 5.5 -4.5"/></svg>
      <span>support@nbguild.org</span>
    </li>
    <li>
      <svg class="icon" viewBox="0 0 21 21" aria-hidden="true"><circle cx="10.5" cy="10.5" r="10.5"/>
        <circle class="glyph" cx="10.5" cy="10.5" r="5.5"/><path class="glyph" d="M5 10.5 h11 M10.5 5 c-3 3 -3 8 0 11 M10.5 5 c3 3 3 8 0 11"/></svg>
      <span>www.<span class="accent">builderslinkguild</span>.org</span>
    </li>
  </ul>

  <p class="address">2400 NW Ridgeline Ave<br>Suite #210, Millbrook, OR 97001</p>
</section>

<section class="card card--back" aria-label="Business card back">
  <svg class="card-shape" viewBox="0 0 585 363" aria-hidden="true">
    <path d="M585 0 H181.5 A181.5 181.5 0 0 0 181.5 363 H585 Z"/>
  </svg>
  <div class="back-brand">
    <span class="brand-line--top">NORTHFIELD</span>
    <span class="brand-line--bottom">BUILDERS GUILD</span>
  </div>
</section>

</body>
</html>
```